Nonprofit needs table front banner

Bright Meridian is a disability advocacy organization in Indiana. We are requesting a graphic design for a table front banner 28 inches high and 72 inches long. The banner must incorporate Bright Meridian’s logo, and the logos of our two web projects, AidLantern and Plumvine. (See attached items.) We would also like the banner to incorporate our slogan, and the slogans of AidLantern and Plumvine:

• AidLantern slogan: “Searching for Accessible Support Should Never Feel Like Wandering Through a Maze. With AidLantern, the Right Path Lights Up.”

• Bright Meridian slogan: “Indiana’s Source for Disability News and Information”

• Plumvine slogan: “Where Workers with Disabilities and Inclusive Employers Connect!”

As Bright Meridian is the organization and AidLantern and Plumvine are our projects, we would like Bright Meridian’s logo and slogan to be in the middle, and slightly more prominent. Also, as we are a disability organization, the banner should be designed with basic accessibility in mind. This means large text in a clear font, with good contrast between the text and the background. The text should be in a sans serif font that is clear and easy to read, with no italics or script fonts. There should not be a "busy" picture or pattern behind the text.

Industry/Entity Type

Non-Profit

Font styles to use
Sans Serif

Requirements
Must have
• The banner must incorporate Bright Meridian’s logo, and the logos of our two web projects, AidLantern and Plumvine. (See attached items.) We would also like the banner to incorporate our slogan, and the slogans of AidLantern and Plumvine:
• • AidLantern slogan: “Searching for Accessible Support Should Never Feel Like Wandering Through a Maze. With AidLantern, the Right Path Lights Up.”
• • Bright Meridian slogan: “Indiana’s Source for Disability News and Information”
• • Plumvine slogan: “Where Workers with Disabilities and Inclusive Employers Connect!”
Nice to have
• As Bright Meridian is the organization and AidLantern and Plumvine are our projects, we would like Bright Meridian’s logo and slogan to be in the middle, and slightly more prominent.
Should not have
• No italics or script fonts. There should not be a "busy" picture or pattern behind the text.

```html
<!DOCTYPE html>
<html lang="en">
<head>
<meta charset="utf-8">
<title>Bright Meridian – Table Front Banner</title>
<link rel="stylesheet" href="https://fonts.googleapis.com/css2?family=Poppins:wght@300;400;500&display=swap">
<style>
  :root {
    --brand-blue: #2c54a3;
    --band-blue: #2c54a3;
    --accent-red: #e52a33;
    --accent-fade: rgba(229, 42, 51, 0);
    --paper: #ffffff;
    --frame: #1e1e1e;
    --text-font: "Poppins", Arial, sans-serif;
  }
  html, body {
    margin: 0;
    padding: 0;
    overflow: hidden;
    background: var(--paper);
  }
  .banner {
    position: relative;
    width: 1200px;
    height: 466px;
    box-sizing: border-box;
    border: 2px solid var(--frame);
    background: var(--paper);
    overflow: hidden;
    font-family: var(--text-font);
  }

  .accent-area {
    position: absolute;
  }
  .accent-area--left {
    left: 0;
    top: 0;
    width: 200px;
    height: 250px;
    background: linear-gradient(135deg, var(--accent-red) 0%, var(--accent-fade) 85%);
  }
  .accent-area--right {
    right: 0;
    top: 170px;
    width: 120px;
    height: 138px;
    background: linear-gradient(315deg, var(--accent-red) 0%, var(--accent-fade) 85%);
  }

  .org-mark {
    position: absolute;
    left: 230px;
    top: 58px;
    width: 400px;
    display: flex;
    flex-direction: column;
    align-items: center;
    gap: 22px;
  }
  .org-mark__dot {
    width: 140px;
    height: 140px;
    border-radius: 50%;
    background: var(--brand-blue);
  }
  .org-mark__name {
    font-weight: 500;
    font-size: 40px;
    line-height: 1;
    color: var(--brand-blue);
    white-space: nowrap;
  }

  .org-slogan {
    position: absolute;
    left: 708px;
    top: 142px;
    margin: 0;
    color: var(--brand-blue);
    font-weight: 300;
    font-size: 40px;
    line-height: 44px;
  }
  .org-slogan span { display: block; white-space: nowrap; }
  .org-slogan .line-1 { letter-spacing: -0.5px; }
  .org-slogan .line-2 { letter-spacing: 4px; }
  .org-slogan .line-3 { letter-spacing: 2.4px; }

  .project-band {
    position: absolute;
    left: 0;
    right: 0;
    top: 308px;
    bottom: 0;
    background: var(--band-blue);
    color: var(--paper);
  }
  .project {
    position: absolute;
    top: 32px;
  }
  .project__slogan {
    margin: 0;
    font-weight: 300;
    font-size: 16px;
    line-height: 26px;
  }
  .project__name {
    display: flex;
    align-items: center;
    gap: 8px;
    margin-top: 16px;
    font-weight: 400;
    font-size: 24px;
    line-height: 1;
  }
  .project__dot {
    width: 32px;
    height: 32px;
    border-radius: 50%;
    background: var(--paper);
  }
  .project--aid {
    left: 120px;
    width: 570px;
  }
  .project--plum {
    right: 120px;
    width: 380px;
    text-align: right;
  }
  .project--plum .project__name { justify-content: flex-end; font-size: 30px; }
</style>
</head>
<body>
  <main class="banner">
    <div class="accent-area accent-area--left" role="img" aria-label="Red accent decoration in the upper left corner"></div>
    <div class="accent-area accent-area--right" role="img" aria-label="Red accent decoration on the right edge"></div>

    <div class="org-mark">
      <div class="org-mark__dot"></div>
      <div class="org-mark__name">Bright Meridian</div>
    </div>

    <h1 class="org-slogan">
      <span class="line-1">Indiana’s Source for</span>
      <span class="line-2">Disability News</span>
      <span class="line-3">and Information</span>
    </h1>

    <section class="project-band">
      <div class="project project--aid">
        <p class="project__slogan">Searching for Accessible Support Should Never Feel Like Wandering Through a Maze. With AidLantern, the Right Path Lights Up.</p>
        <div class="project__name"><span class="project__dot"></span>AidLantern</div>
      </div>
      <div class="project project--plum">
        <p class="project__slogan">Where Workers with Disabilities and Inclusive Employers Connect!</p>
        <div class="project__name">Plumvine</div>
      </div>
    </section>
  </main>
</body>
</html>
```